Website for Briar Hollow Gathering Church

Wordpress website design required for Briar Hollow Gathering Church. We are a family oriented church catering for age groups from school age to elderly people. The church has a wide variety of activities which it coordinates. The idea is to describe the activities on the activities page, but cross-link them to show which would be applicable to the different age groups.

We would like an inviting website which is easy to read and navigate.

Target Market(s)

Very wide audience - from school age youth to elderly people, so design and style should cater for both audiences.

Industry/Entity Type

Church

Coding

Coded - Design and coding required

Number of Pages Required

5+ page

Font styles to use
Sans Serif

Colors
0255a3
ffffff
0792cd
f78f20

Requirements
Must have
• Inviting website.
• Clear readable font.
• Space to import photos to balance text on each page.
• Need to project a dynamic and progressive feel for the church.
• Easy to navigate.
Nice to have
• Scrolling photos on pages. Ability to enter questions/ comments/prayer requests on Home page.
Should not have
• Conservative audience, so should not be too bold.

```html
<!DOCTYPE html>
<html lang="en">
<head>
<meta charset="utf-8">
<title>Briar Hollow Gathering Church</title>
<link rel="stylesheet" href="https://fonts.googleapis.com/css2?family=Open+Sans:ital,wght@0,400;0,600;0,700;1,400&display=swap">
<style>
:root{
  --navy:#0b4a9c;
  --brand:#0255a3;
  --sky:#0792cd;
  --orange:#f78f20;
  --orange-text:#e8792a;
  --ink:#333;
  --muted:#666;
  --pale:#f1f1f1;
  --footer:#141414;
  --white:#fff;
}
*{box-sizing:border-box;margin:0;padding:0}
html,body{width:724px;height:1200px;overflow:hidden}
body{font-family:"Open Sans",Arial,sans-serif;color:var(--ink);background:var(--white);position:relative}
.wrap{width:565px;margin:0 auto;position:relative}
.site-header{height:101px}
.brand{position:absolute;left:0;top:56px;display:flex;align-items:center;gap:6px}
.brand-dot{width:10px;height:10px;border-radius:50%;background:var(--brand)}
.brand-name{font-size:13px;font-weight:600;color:var(--brand)}
.header-contact{position:absolute;right:24px;top:14px;text-align:right;font-size:8px;color:#222;line-height:1.3}
.header-contact strong{display:block;font-size:11px;font-weight:400;color:#111}
.phone-badge{position:absolute;right:0;top:16px;width:20px;height:20px;border:1px solid #bbb;border-radius:50%;display:flex;align-items:center;justify-content:center}
.partner{position:absolute;right:0;top:60px;display:flex;align-items:center;gap:6px}
.partner-mark{width:26px;height:26px;border-radius:50%;background:#1a1a1a}
.partner-name{font-size:10px;color:#111;border-bottom:1.5px solid #d2232a;padding-bottom:2px;width:148px}
.main-nav{height:24px;background:var(--navy)}
.main-nav ul{list-style:none;display:flex;height:24px}
.main-nav li{font-size:8px;color:var(--white);line-height:24px;padding:0 14px 0 13px}
.main-nav li:nth-child(n+2){padding:0 18px 0 20px}
.main-nav li.current{background:var(--sky)}
.hero{height:245px;position:relative;background:linear-gradient(100deg,#c9b89a 0%,#e8d6b4 30%,#b8a78a 55%,#9a8a72 80%,#7d6d5a 100%)}
.hero-arrow{position:absolute;top:114px;width:15px;height:20px;background:#555;opacity:.7}
.hero-arrow.prev{left:0}.hero-arrow.next{right:0}
.hero-caption{position:absolute;left:80px;top:202px;width:565px;height:31px;background:rgba(130,120,80,.75);color:var(--white);font-size:10.5px;font-weight:600;text-align:center;line-height:31px}
.welcome{height:161px;text-align:center;padding-top:28px}
.section-title{font-size:16px;font-weight:600;color:var(--orange-text)}
.welcome p{font-size:7px;line-height:11.7px;color:var(--muted);margin-top:7px}
.btn-outline{display:inline-block;margin-top:10px;border:1px solid #bbb;font-size:6.5px;padding:5px 7px;color:#444}
.minister{height:106px;background:linear-gradient(90deg,#3a2b3e,#5a3e3e 40%,#3b2c40 70%,#2c2238);text-align:center;padding-top:27px}
.minister .section-title{color:var(--orange)}
.minister blockquote{font-size:9px;font-style:italic;color:#eee;line-height:13.5px;width:430px;margin:6px auto 0}
.news{height:135px;background:var(--pale);padding-top:24px}
.news-head{display:flex;justify-content:space-between;align-items:center}
.news-head h2{font-size:16px;font-weight:600;color:var(--sky)}
.view-all{background:#333;color:var(--white);font-size:5.5px;padding:3px 4px}
.news-list{display:flex;justify-content:space-between;margin-top:10px}
.news-item{width:173px;height:48px;background:var(--white);display:flex}
.news-date{width:28px;background:var(--sky);color:var(--white);text-align:center;font-weight:700;padding-top:8px;line-height:1}
.news-date b{display:block;font-size:13px}
.news-date span{font-size:7.5px}
.news-item p{font-size:7px;line-height:10.5px;padding:8px 10px;color:#222}
.service{text-align:center;padding-top:36px;height:78px}
.service h2{font-size:16px;font-weight:600;color:var(--navy);display:flex;align-items:center;justify-content:center;gap:4px}
.service p{font-size:7.5px;color:var(--navy);margin-top:5px}
.rule{height:1px;background:#ddd}
.theme{text-align:center;height:112px;padding-top:20px}
.theme p{font-size:8.5px;color:var(--muted);line-height:14.5px;margin-top:4px}
.info-strip{height:41px;background:var(--pale);display:flex;justify-content:center;align-items:center;gap:36px;font-size:7.5px;color:#444}
.info-strip span{display:flex;align-items:center;gap:4px}
.forms{display:flex;height:139px}
.form-panel{width:50%;padding:17px 0 0 79px}
.form-panel.prayer{background:var(--navy)}
.form-panel.contact{background:var(--sky);padding-left:27px}
.form-panel h3{font-size:13px;font-weight:400;color:var(--white);display:flex;align-items:center;gap:5px}
.field-row{display:flex;gap:5px;margin-top:8px}
.field{background:var(--white);height:24px;width:125px;font-size:7.5px;color:#444;padding:7px 10px}
.field.wide{width:255px;margin-top:10px}
.btn-subscribe{display:inline-block;background:var(--orange);color:#222;font-size:7.5px;font-weight:600;padding:6px 9px;margin-top:8px}
.btn-submit{display:inline-block;background:#161616;color:var(--white);font-size:7.5px;font-weight:600;padding:6px 9px;margin-top:9px}
.prayer-note{font-size:7px;color:#7fb0e8;line-height:10.5px;margin-top:10px;width:250px}
.site-footer{height:58px;background:var(--footer);padding-top:19px;position:relative}
.footer-nav{font-size:6.5px;color:#aaa}
.copyright{font-size:6.5px;color:#aaa;margin-top:8px}
.social{position:absolute;right:0;top:-4px;display:flex;gap:4px}
.social span{width:15px;height:15px;border-radius:50%}
</style>
</head>
<body>
<header class="site-header">
  <div class="wrap">
    <div class="brand"><span class="brand-dot"></span><span class="brand-name">Briar Hollow Gathering Church</span></div>
    <div class="header-contact">14 Larkfield Rd, Briar Hollow, WA 6190<strong>Phone : (08) 9400 2718</strong></div>
    <div class="phone-badge"><svg width="9" height="9" viewBox="0 0 24 24"><path fill="#333" d="M6.6 10.8c1.4 2.8 3.8 5.1 6.6 6.6l2.2-2.2c.3-.3.7-.4 1-.2 1.1.4 2.3.6 3.6.6.6 0 1 .4 1 1V20c0 .6-.4 1-1 1C10.6 21 3 13.4 3 4c0-.6.4-1 1-1h3.5c.6 0 1 .4 1 1 0 1.3.2 2.5.6 3.6.1.3 0 .7-.2 1z"/></svg></div>
    <div class="partner"><span class="partner-mark"></span><span class="partner-name">Fellowship of Hollow Churches</span></div>
  </div>
</header>
<nav class="main-nav">
  <div class="wrap">
    <ul><li class="current">Home</li><li>Age Group</li><li>Activities</li><li>Events</li><li>About BHGC</li><li>Contact</li></ul>
  </div>
</nav>
<section class="hero" role="img" aria-label="Photo of smiling older church members outdoors in warm sunset light">
  <span class="hero-arrow prev"></span><span class="hero-arrow next"></span>
  <div class="hero-caption">Morbi et justo consequat, dapibus mi quis, tempor turpis. Vivamus blandit est et porta consequat.</div>
</section>
<section class="welcome">
  <div class="wrap">
    <h1 class="section-title">Welcome to Briar Hollow Gathering Church</h1>
    <p>Aliquam iaculis orci nisi, a lacinia metus semper feugiat. Vivamus ut orci vitae est aliquam molestie id vel massa. Ut cursus libero gravida justo posuere, vel pretium sapien rutrum. Nulla nec aliquet massa. Nunc euismod leo id felis vestibulum, nec aliquam orci vehicula. Vestibulum aliquet tortor vehicula erat commodo, fermentum ullamcorper magna vulputate. Duis dictum pretium sem, ac cursus est cursus vitae. Vestibulum auctor, neque nec luctus interdum, tortor nibh posuere lectus, sed vulputate urna tellus eu purus. Sed dictum faucibus posuere. Nunc venenatis hendrerit mi. Sed in ipsum vel leo faucibus porta ac sed ligula.</p>
    <span class="btn-outline">Read more</span>
  </div>
</section>
<section class="minister" role="img" aria-label="Blurred warm background photo of a church interior">
  <h2 class="section-title">Minister's weekly message</h2>
  <blockquote>“ Nam pretium, sem ut ultrices suscipit, augue turpis pretium quam, quis dapibus mi nisl eu metus odio id massa maximus congue in non turpis ”</blockquote>
</section>
<section class="news">
  <div class="wrap">
    <div class="news-head"><h2>News</h2><span class="view-all">View All</span></div>
    <div class="news-list">
      <article class="news-item"><div class="news-date"><b>19</b><span>OCT</span></div><p>Aliquam iaculis orci nisi, a lacinia metus semper feugiat. Vivamus ut orci vitae est aliquam molestie.</p></article>
      <article class="news-item"><div class="news-date"><b>19</b><span>OCT</span></div><p>Aliquam iaculis orci nisi, a lacinia metus semper feugiat. Vivamus ut orci vitae est aliquam molestie.</p></article>
      <article class="news-item"><div class="news-date"><b>19</b><span>OCT</span></div><p>Aliquam iaculis orci nisi, a lacinia metus semper feugiat. Vivamus ut orci vitae est aliquam molestie.</p></article>
    </div>
  </div>
</section>
<section class="service">
  <h2><svg width="12" height="12" viewBox="0 0 24 24"><circle cx="12" cy="12" r="9.5" fill="none" stroke="#0b4a9c" stroke-width="3"/><path d="M12 6v6l4 2" fill="none" stroke="#0b4a9c" stroke-width="2.5"/></svg>Service Times</h2>
  <p>Mon - Fri : 10 AM to 7 PM &nbsp;&nbsp;&nbsp; / &nbsp;&nbsp;&nbsp; Sat -Sun : 10.30 AM to 6 Pm</p>
</section>
<div class="wrap rule"></div>
<section class="theme">
  <div class="wrap">
    <h2 class="section-title">Theme</h2>
    <p>Aliquam a enim ac tortor euismod euismod eu eu tellus. Cras molestie nec dui sed eleifend. Cum sociis natoque penatibus et magnis dis parturient montes, nascetur ridiculus mus. Cras mollis sit amet leo a pharetra. Vivamus sed fringilla eros, porttitor aliquet felis. Duis nec magna nisi. Nulla venenatis volutpat dapibus.</p>
  </div>
</section>
<section class="info-strip">
  <span><svg width="7" height="8" viewBox="0 0 24 24"><path fill="#444" d="M12 2a7 7 0 0 0-7 7c0 5 7 13 7 13s7-8 7-13a7 7 0 0 0-7-7zm0 9.5a2.5 2.5 0 1 1 0-5 2.5 2.5 0 0 1 0 5z"/></svg>24 Building name, Street name, City - Zipcode</span>
  <span><svg width="5" height="8" viewBox="0 0 10 16"><rect x="1" y="1" width="8" height="14" rx="1.5" fill="none" stroke="#444" stroke-width="2"/></svg>Phone : 546 321 65485</span>
  <span><svg width="9" height="7" viewBox="0 0 18 13"><rect width="18" height="13" fill="#444"/><path d="M0 0l9 7 9-7" fill="none" stroke="#f1f1f1" stroke-width="1.5"/></svg>Email : hello@briarhollow.org</span>
</section>
<section class="forms">
  <div class="form-panel prayer">
    <h3><svg width="12" height="12" viewBox="0 0 24 24"><rect x="2" y="5" width="16" height="16" rx="2" fill="none" stroke="#fff" stroke-width="2.2"/><path d="M10 14l1-4 9-8 3 3-9 8z" fill="#fff"/></svg>Prayer request</h3>
    <div class="field-row"><div class="field">Name</div><div class="field">Email</div></div>
    <span class="btn-subscribe">Subscribe</span>
    <p class="prayer-note">Aliquam iaculis orci nisi, a lacinia metus semper feugiat. Vivamus ut orci vitae est aliquam molestie.</p>
  </div>
  <div class="form-panel contact">
    <h3><svg width="13" height="10" viewBox="0 0 18 13"><rect width="18" height="13" rx="1" fill="#fff"/><path d="M0 1l9 7 9-7" fill="none" stroke="#0792cd" stroke-width="1.5"/></svg>Contact Us</h3>
    <div class="field-row"><div class="field">Name</div><div class="field">Email</div></div>
    <div class="field wide">Questions/ Comments</div>
    <span class="btn-submit">Submit</span>
  </div>
</section>
<footer class="site-footer">
  <div class="wrap">
    <div class="footer-nav">Home &nbsp;| &nbsp;Age Group &nbsp;| &nbsp;Activities &nbsp;| &nbsp;Events &nbsp;| &nbsp;About BHGC &nbsp;| &nbsp;Contact</div>
    <div class="copyright">Copyright © 2016 BHGC - Briar Hollow Gathering Church. &nbsp;All rights reserved.</div>
    <div class="social"><span style="background:#2a4f9a"></span><span style="background:#1d8fe0"></span></div>
  </div>
</footer>
</body>
</html>
```